full stationary design for a modern sleek design company

we are a design company that does modern minimalistic interior design works as well as other design services for high end clients.
we need a full stationary design including and not limited to (double sided business card, letter head, envelopes, documents folder...etc) that reflects the modern style design we do.
sleek modern and minimalistic is the requirements.
Updates

please use the latest attached files as there was a slight modification on the logo Added Wednesday, March 1, 2017

minor update on the logo files in JPG and PSD has been updated kindly follow the new attachments. Added Thursday, March 2, 2017

Target Market(s)

modern minimalist clients

Industry/Entity Type

Design Agency

Requirements
Must have
• the logo
Nice to have
• i like the colors in the colored 3D logo attached
Should not have
• too many colors

```html
<!DOCTYPE html>
<html lang="en">
<head>
<meta charset="utf-8">
<title>Norvane Studio Letterhead</title>
<link href="https://fonts.googleapis.com/css2?family=Exo+2:wght@600&family=Roboto:wght@400&display=swap" rel="stylesheet">
<style>
  :root {
    --backdrop: #efe4d1;
    --paper: #ffffff;
    --ink: #2b2b2b;
    --accent: #e0702a;
    --accent-deep: #c95f22;
    --steel: #b9bcc2;
    --watermark: #ececec;
    --tile: #f7e6dc;
    --muted: #6b6b6b;
  }
  * { margin: 0; padding: 0; box-sizing: border-box; }
  html, body {
    width: 1200px; height: 784px; overflow: hidden;
    background: var(--backdrop);
  }
  .letterhead {
    position: absolute; left: 338px; top: 22px;
    width: 523px; height: 740px;
    background: var(--paper);
    box-shadow: 0 2px 10px rgba(120, 90, 50, 0.18);
    overflow: hidden;
  }
  .header-rule-start {
    position: absolute; left: 0; top: 24px; width: 24px; height: 3px;
    background: var(--steel);
  }
  .brand {
    position: absolute; left: 30px; top: 14px;
    font-family: "Exo 2", sans-serif; font-weight: 600;
  }
  .brand-name {
    display: flex; align-items: center; gap: 6px;
    font-size: 17px; letter-spacing: 0.5px; color: var(--ink);
    text-transform: uppercase; line-height: 1;
  }
  .brand-mark {
    width: 12px; height: 12px; background: var(--accent);
  }
  .brand-tagline {
    margin-top: 3px; padding-left: 40px;
    font-size: 8px; letter-spacing: 3.4px; color: var(--accent);
    text-transform: uppercase;
  }
  .header-rule-accent {
    position: absolute; left: 214px; top: 24px; width: 98px; height: 3px;
    background: var(--accent);
  }
  .contact {
    position: absolute; left: 318px; top: 17px; width: 130px;
    font-family: "Roboto", sans-serif; font-size: 5.5px; line-height: 8px;
    color: var(--muted); list-style: none;
  }
  .contact li::before {
    content: ""; display: inline-block; width: 3px; height: 3px;
    margin-right: 3px; background: var(--accent); vertical-align: middle;
  }
  .header-rule-end {
    position: absolute; right: 0; top: 24px; width: 68px; height: 3px;
    background: var(--steel);
  }
  .footer-tiles { position: absolute; left: 0; bottom: 6px; }
  .footer-watermark {
    position: absolute; left: 14px; bottom: 2px;
    font-family: "Exo 2", sans-serif; font-weight: 600;
    font-size: 68px; letter-spacing: 2px; line-height: 1;
    color: var(--watermark); text-transform: uppercase; white-space: nowrap;
  }
  .footer-band-accent {
    position: absolute; left: 0; bottom: 0; width: 73%; height: 7px;
    background: linear-gradient(to right, var(--accent-deep), var(--accent));
  }
  .footer-band-steel {
    position: absolute; right: 0; bottom: 0; width: 27%; height: 7px;
    background: linear-gradient(to right, var(--steel), #d8dade);
  }
</style>
</head>
<body>
  <main class="letterhead">
    <div class="header-rule-start"></div>
    <div class="brand">
      <div class="brand-name"><span class="brand-mark"></span>Norvane Studio</div>
      <div class="brand-tagline">By Elise Marrow</div>
    </div>
    <div class="header-rule-accent"></div>
    <ul class="contact">
      <li>12 Harlow Lane, Suite 400, Austin TX 000</li>
      <li>(000) 555-0142 &nbsp; (000) 555-0187</li>
      <li>hello@norvanestudio.com &nbsp; www.norvanestudio.com</li>
    </ul>
    <div class="header-rule-end"></div>

    <svg class="footer-tiles" width="523" height="150" viewBox="0 0 523 150" aria-hidden="true">
      <rect x="250" y="10" width="38" height="38" rx="5" fill="var(--tile)" opacity="0.7"/>
      <rect x="296" y="22" width="62" height="62" rx="6" fill="var(--tile)" opacity="0.5"/>
      <rect x="262" y="62" width="40" height="40" rx="5" fill="var(--tile)" opacity="0.6"/>
      <rect x="318" y="96" width="48" height="48" rx="5" fill="var(--tile)" opacity="0.45"/>
      <rect x="366" y="50" width="30" height="30" rx="4" fill="var(--tile)" opacity="0.4"/>
    </svg>
    <div class="footer-watermark">Norvane Studio</div>
    <div class="footer-band-accent"></div>
    <div class="footer-band-steel"></div>
  </main>
</body>
</html>
```